Business Card for Multi-Brand Sportswear Company

We are looking for a business card which represents our company and the multiple brands within it.

The company: Fen Athletics (LTD)
The brands: Fen, TavaPuni, ElmStretch, Grit and Rain

Employees using these cards would be representing Fen Athletics, rather than any of the individual brands. You will see a current design within the uploaded files, to give some inspiration. The actual text of the brands is not necessary, but the logos should be on there is some format.

Our creative minds on this are stretched, so we are looking for someone to make this their own, and show us what a good business card should look like.

We may like to get these printed with spot gloss, so keep that in mind with your designs.

www.fenathletics.co.uk

Industry/Entity Type

Business

Contact Information for Business Card

Leo Pemberton-Hale
Operations Manager
(+44) 1632 960 418
Leo@fenathletics.co.uk
www.fenathletics.co.uk

Font styles to use
Sans Serif
Other font styles liked:
• Eurostile

Colors
ffffff

Requirements
Nice to have
• Dark (black) background

```html
<!DOCTYPE html>
<html lang="en">
<head>
<meta charset="utf-8">
<title>Fen Athletics business card</title>
<link rel="stylesheet" href="https://fonts.googleapis.com/css2?family=Questrial&display=swap">
<style>
  :root {
    --backdrop: #8c8c8c;
    --card: #1f2021;
    --red: #e02327;
    --white: #ffffff;
    --ink-dark: #1f2021;
    --brand-violet: #8f7c90;
    --brand-grey: #9a9a9a;
  }
  * { margin: 0; padding: 0; box-sizing: border-box; }
  html, body {
    width: 1200px;
    height: 854px;
    overflow: hidden;
    background: var(--backdrop);
    font-family: "Questrial", sans-serif;
  }
  .card {
    position: absolute;
    top: 289px;
    width: 512px;
    height: 293px;
    background: var(--card);
    overflow: hidden;
  }
  .card--front { left: 69px; }
  .card--back { left: 600px; }
  .card__bands {
    position: absolute;
    inset: 0;
    width: 512px;
    height: 293px;
  }
  .band { fill: var(--red); }

  .holder {
    position: absolute;
    left: 35px;
    top: 73px;
    width: 196px;
    color: var(--white);
    text-align: right;
  }
  .holder__name {
    font-size: 19px;
    letter-spacing: -0.2px;
    text-align: left;
  }
  .holder__title {
    margin-top: 8px;
    font-size: 15px;
  }
  .contact {
    position: absolute;
    right: 41px;
    top: 73px;
    list-style: none;
    color: var(--white);
    font-size: 14px;
    line-height: 24px;
    text-align: right;
  }
  .band-wordmark {
    position: absolute;
    right: 84px;
    top: 192px;
    font-size: 14px;
    letter-spacing: 1px;
    color: var(--ink-dark);
    text-transform: uppercase;
  }
  .brands {
    position: absolute;
    left: 100px;
    width: 314px;
    top: 244px;
    display: flex;
    justify-content: center;
    align-items: center;
    gap: 14px;
    list-style: none;
    font-size: 11px;
  }
  .brands__item--tavapuni { color: var(--brand-violet); }
  .brands__item--grit { color: var(--red); }
  .brands__item--fen { color: var(--white); }
  .brands__item--elm { color: var(--brand-grey); }

  .wordmark {
    position: absolute;
    right: 24px;
    top: 98px;
    font-size: 38px;
    letter-spacing: 2px;
    color: var(--white);
    text-transform: uppercase;
    white-space: nowrap;
  }
</style>
</head>
<body>

<section class="card card--front" aria-label="Card front">
  <svg class="card__bands" viewBox="0 0 598 342" aria-hidden="true">
    <polygon class="band" points="0,211 24,211 0,238"/>
    <polygon class="band" points="45,211 68,211 23,261 0,261"/>
    <polygon class="band" points="77,211 100,211 55,261 32,261"/>
    <polygon class="band" points="110,211 133,211 88,261 65,261"/>
    <polygon class="band" points="155,211 549,211 504,261 110,261"/>
  </svg>

  <div class="holder">
    <p class="holder__name">Leo Pemberton-Hale</p>
    <p class="holder__title">Operations Manager</p>
  </div>

  <ul class="contact">
    <li>(+44) 1632 960 418</li>
    <li>Leo@fenathletics.co.uk</li>
    <li>www.fenathletics.co.uk</li>
  </ul>

  <p class="band-wordmark">Fen Athletics</p>

  <ul class="brands">
    <li class="brands__item brands__item--tavapuni">TavaPuni</li>
    <li class="brands__item brands__item--grit">Grit and Rain</li>
    <li class="brands__item brands__item--fen">Fen</li>
    <li class="brands__item brands__item--elm">ElmStretch</li>
  </ul>
</section>

<section class="card card--back" aria-label="Card back">
  <svg class="card__bands" viewBox="0 0 598 342" aria-hidden="true">
    <polygon class="band" points="0,248 45,248 0,297"/>
    <polygon class="band" points="57,248 95,248 44,299 6,299"/>
    <polygon class="band" points="107,248 140,248 89,299 56,299"/>
    <polygon class="band" points="152,248 180,248 129,299 101,299"/>
    <polygon class="band" points="200,248 569,248 518,299 149,299"/>
  </svg>

  <p class="wordmark">Fen Athletics</p>
</section>

</body>
</html>
```